eCommerce Website Design for Children's Book Service

I am looking for a 5 page eCommerce website that includes a Shopping Cart. 'Lumiva Books' is the title of the company and its logo is attached. 'Sprouting wonder in words,' is the company's motto and 'spring green' is the main color. The website needs to appeal to families. Images of books and/or maple seeds (helicopter seeds) moving are part of the graphics.
Updates

I have updated my brief and I would like my website design to include 5 pages: home, about, products (books), blog, contact. WordPress is the web format that I am most comfortable with.

Target Market(s)

Families with young children

Coding

Coded - Design and coding required

Number of Pages Required

5+ page

Requirements
Must have
• Shopping cart page; contact page, books page with spaces of photos to go, blog page; spring green color
Nice to have
• A graphic that relates to motto : "sprouting wonder in words"
• WordPress

```html
<!DOCTYPE html>
<html lang="en">
<head>
<meta charset="utf-8">
<title>Lumiva Books – Sprouting Wonder in Words</title>
<link href="https://fonts.googleapis.com/css2?family=Lato:ital,wght@0,400;0,700;0,900;1,400&display=swap" rel="stylesheet">
<style>
:root{
  --green:#6ab445;
  --green-dark:#4f9a34;
  --green-band:#5fae45;
  --green-deep:#3f8a2c;
  --ink:#333333;
  --muted:#555555;
  --line:#dddddd;
  --star:#f08a24;
  --footer:#2e2e2e;
  --footer-base:#222222;
  --white:#ffffff;
}
*{box-sizing:border-box;margin:0;padding:0}
html,body{width:1200px;height:2338px;overflow:hidden}
body{font-family:'Lato',sans-serif;color:var(--ink);background:var(--white);position:relative}
a{color:inherit;text-decoration:none}

/* header */
.site-header{position:absolute;left:0;top:0;width:1200px;height:143px;z-index:2}
.brand-badge{position:absolute;left:70px;top:-10px;width:190px;height:210px;border-radius:0 0 95px 95px;background:var(--white);display:flex;flex-direction:column;align-items:center;justify-content:flex-end;padding-bottom:42px;box-shadow:0 4px 8px rgba(0,0,0,.12)}
.brand-name{font-size:34px;font-weight:700;color:var(--green-dark);line-height:1}
.utility-links{position:absolute;right:75px;top:18px;display:flex;gap:18px;font-size:12px;font-weight:700;color:#444;text-transform:uppercase}
.utility-links span{display:flex;align-items:center;gap:5px}
.search-box{position:absolute;left:495px;top:36px;width:295px;height:36px;border:1px solid #999;display:flex;align-items:center;justify-content:space-between;padding:0 12px 0 16px;font-size:13px;color:#555}
.call-us{position:absolute;right:75px;top:52px;font-size:20px;font-weight:700;color:#444;display:flex;align-items:center;gap:8px}
.call-us .number{color:var(--green-dark)}
.main-nav{position:absolute;left:280px;top:101px;width:920px;height:42px;background:var(--green);clip-path:polygon(30px 0,100% 0,100% 100%,0 100%);display:flex;align-items:center}
.main-nav ul{list-style:none;display:flex;gap:44px;padding-left:38px;font-size:14px;font-weight:700;color:var(--white);text-transform:uppercase}
.cart-total{position:absolute;left:991px;top:101px;width:209px;height:42px;background:var(--green-dark);clip-path:polygon(18px 0,100% 0,100% 100%,0 100%);display:flex;align-items:center;justify-content:center;gap:9px;color:var(--white);font-size:16px;font-weight:700}

/* hero */
.hero{position:absolute;left:0;top:143px;width:1200px;height:496px}
.hero-photo{position:absolute;inset:0;background:linear-gradient(100deg,#c9b8a6 0%,#a89c94 35%,#d9c8be 55%,#8f9499 75%,#b7bcc0 100%)}
.hero-photo::after{content:"";position:absolute;left:310px;top:330px;width:520px;height:166px;background:linear-gradient(90deg,#d9cf3c,#e6dc55);opacity:.8}
.hero-title{position:absolute;left:0;right:0;top:200px;text-align:center;font-size:52px;font-weight:900;line-height:1.1;color:var(--white);text-transform:uppercase;text-shadow:0 2px 6px rgba(0,0,0,.35)}
.hero-dots{position:absolute;left:568px;top:423px;display:flex;gap:8px}
.hero-dots i{width:10px;height:10px;border-radius:50%;background:#bbb}
.hero-dots i:first-child{background:var(--green)}

/* featured */
.featured{position:absolute;left:75px;top:686px;width:1050px}
.section-title{font-size:22px;font-weight:700;text-transform:uppercase;color:var(--ink)}
.view-all{position:absolute;right:0;top:-2px;width:106px;height:34px;border:2px solid var(--green-dark);font-size:11px;font-weight:700;display:flex;align-items:center;justify-content:center}
.product-grid{position:absolute;top:59px;left:0;display:flex;gap:26px}
.product-card{width:243px;height:327px;border:1px solid var(--line);background:var(--white);position:relative;padding:0 17px}
.book-cover{width:128px;height:168px;margin:12px auto 0;display:block;border-radius:2px 5px 5px 2px;box-shadow:4px 4px 0 rgba(0,0,0,.15)}
.product-name{margin-top:16px;font-size:15px;font-weight:700;text-transform:uppercase}
.product-sub{font-size:14px;color:var(--muted);margin-top:3px}
.stars{color:var(--star);font-size:15px;letter-spacing:2px;margin-top:2px}
.product-foot{position:absolute;left:17px;right:20px;bottom:18px;display:flex;justify-content:space-between;align-items:center}
.price{font-size:22px;font-weight:700;color:var(--green-dark)}
.btn-outline{width:118px;height:36px;border:2px solid var(--green-dark);color:var(--green-dark);font-size:13px;font-weight:700;display:flex;align-items:center;justify-content:center;text-transform:uppercase}

/* welcome */
.welcome{position:absolute;left:0;top:1134px;width:1200px;height:327px;background:linear-gradient(90deg,var(--green-deep),var(--green-band) 50%,#6ab84e);color:var(--white);text-align:center}
.welcome h2{margin-top:44px;font-size:21px;font-weight:700;text-transform:uppercase}
.welcome p{width:930px;margin:18px auto 0;font-size:14.5px;line-height:31px}
.btn-light{display:inline-flex;margin-top:30px;width:150px;height:42px;border:2px solid var(--white);align-items:center;justify-content:center;font-size:14px;font-weight:700;text-transform:uppercase}

/* testimonials */
.testimonials{position:absolute;left:0;top:1505px;width:1200px;text-align:center}
.testimonial-box{position:absolute;left:217px;top:55px;width:766px;height:197px;border:3px solid #e6e6e6;background:var(--white);padding:16px 40px}
.quote-mark{font-size:60px;font-weight:900;color:#ccc;line-height:.9;height:34px}
.testimonial-box p{font-style:italic;font-size:16px;line-height:28px;color:#333;margin-top:8px}
.testimonial-author{margin-top:12px;font-size:14px;color:var(--green-dark);text-transform:uppercase}
.slider-arrow{position:absolute;top:138px;color:var(--green)}

/* features */
.features{position:absolute;left:75px;top:1823px;display:flex;gap:13px}
.feature{width:252px;height:112px;border:2px solid var(--green);display:flex;align-items:center;gap:22px;padding-left:12px}
.feature-text{font-size:21px;font-weight:700;color:var(--green-dark);line-height:1.22;text-transform:uppercase}

/* footer */
.site-footer{position:absolute;left:0;top:1986px;width:1200px;height:289px;background:var(--footer);color:#ddd}
.footer-brand{position:absolute;left:75px;top:130px;font-size:34px;font-weight:700;color:var(--green)}
.footer-col{position:absolute;top:52px}
.footer-col h3{font-size:15px;font-weight:700;color:var(--white);text-transform:uppercase;margin-bottom:12px}
.footer-col li{list-style:none;font-size:14px;line-height:28px}
.email-field{width:242px;height:42px;background:var(--white);color:#444;font-size:15px;display:flex;align-items:center;padding-left:12px}
.btn-signup{margin:18px 0 0 153px;width:89px;height:38px;background:var(--green);color:var(--white);font-size:14px;font-weight:700;display:flex;align-items:center;justify-content:center}
.social{display:flex;gap:16px;margin:22px 0 0 0;padding-left:0}
.social span{width:18px;height:18px;border-radius:50%;background:#e6e6e6;display:block}
.footer-base{position:absolute;left:0;top:2275px;width:1200px;height:63px;background:var(--footer-base);color:#999;font-size:13px;display:flex;align-items:center;justify-content:center}
</style>
</head>
<body>

<header class="site-header">
  <div class="brand-badge"><span class="brand-name">Lumiva Books</span></div>
  <nav class="utility-links">
    <span><svg width="10" height="11" viewBox="0 0 10 11"><rect x="1" y="5" width="8" height="6" fill="#444"/><path d="M3 5V3a2 2 0 0 1 4 0v2" stroke="#444" stroke-width="1.5" fill="none"/></svg>Log In</span>
    <span><svg width="11" height="11" viewBox="0 0 11 11"><circle cx="5.5" cy="3" r="2.6" fill="#444"/><path d="M0.5 11a5 5 0 0 1 10 0z" fill="#444"/></svg>Register</span>
    <span><svg width="12" height="11" viewBox="0 0 12 11"><path d="M6 10.5 1 5.5A2.8 2.8 0 0 1 6 2a2.8 2.8 0 0 1 5 3.5z" fill="#444"/></svg>Wishlist</span>
    <span><svg width="11" height="11" viewBox="0 0 11 11"><circle cx="5.5" cy="5.5" r="5.5" fill="#444"/><text x="5.5" y="8.5" font-size="8" font-weight="700" text-anchor="middle" fill="#fff" font-family="Lato,sans-serif">?</text></svg>FAQ</span>
  </nav>
  <div class="search-box">Search Products
    <svg width="16" height="16" viewBox="0 0 16 16"><circle cx="6.5" cy="6.5" r="5" stroke="#444" stroke-width="2" fill="none"/><path d="M10.5 10.5 15 15" stroke="#444" stroke-width="2.4"/></svg>
  </div>
  <div class="call-us">
    <svg width="17" height="17" viewBox="0 0 24 24"><path d="M6.6 10.8a15 15 0 0 0 6.6 6.6l2.2-2.2a1 1 0 0 1 1-.25 11.4 11.4 0 0 0 3.6.57 1 1 0 0 1 1 1V20a1 1 0 0 1-1 1A17 17 0 0 1 3 4a1 1 0 0 1 1-1h3.5a1 1 0 0 1 1 1c0 1.25.2 2.45.57 3.57a1 1 0 0 1-.25 1z" fill="#444"/></svg>
    CALL US: <span class="number">1-80-555-0142</span>
  </div>
  <nav class="main-nav">
    <ul><li>Home</li><li>About Us</li><li>Books</li><li>Shop</li><li>Reviews</li><li>Contact Us</li></ul>
  </nav>
  <div class="cart-total">
    <svg width="18" height="16" viewBox="0 0 18 16"><path d="M0 1h3l2.5 9h9L17 4H5" stroke="#fff" stroke-width="2" fill="none"/><circle cx="7" cy="14" r="1.6" fill="#fff"/><circle cx="13" cy="14" r="1.6" fill="#fff"/></svg>
    $00.00
  </div>
</header>

<section class="hero">
  <div class="hero-photo" role="img" aria-label="Photo of a mother reading a colourful picture book with her baby on a sofa"></div>
  <h1 class="hero-title">Sprouting Wonder<br>in Words</h1>
  <div class="hero-dots"><i></i><i></i><i></i><i></i></div>
</section>

<section class="featured">
  <h2 class="section-title">Featured Products</h2>
  <a class="view-all">VIEW ALL &nbsp;&gt;&gt;</a>
  <div class="product-grid">
    <article class="product-card">
      <div class="book-cover" role="img" aria-label="Lime green book cover" style="background:linear-gradient(90deg,#6f9a1c 0 10%,#9cc42a 10%)"></div>
      <h3 class="product-name">Product Name</h3>
      <p class="product-sub">Cupidatat non proident</p>
      <div class="stars">★★★★★</div>
      <div class="product-foot"><span class="price">$8.00</span><a class="btn-outline">Add to Cart</a></div>
    </article>
    <article class="product-card">
      <div class="book-cover" role="img" aria-label="Purple book cover" style="background:linear-gradient(90deg,#3e2a5e 0 10%,#6a4a97 10%)"></div>
      <h3 class="product-name">Product Name</h3>
      <p class="product-sub">Cupidatat non proident</p>
      <div class="stars">★★★★★</div>
      <div class="product-foot"><span class="price">$8.00</span><a class="btn-outline">Add to Cart</a></div>
    </article>
    <article class="product-card">
      <div class="book-cover" role="img" aria-label="Grey green book cover" style="background:linear-gradient(90deg,#3f4d3c 0 10%,#5d6e58 10%)"></div>
      <h3 class="product-name">Product Name</h3>
      <p class="product-sub">Cupidatat non proident</p>
      <div class="stars">★★★★★</div>
      <div class="product-foot"><span class="price">$8.00</span><a class="btn-outline">Add to Cart</a></div>
    </article>
    <article class="product-card">
      <div class="book-cover" role="img" aria-label="Green book cover" style="background:linear-gradient(90deg,#2e5f26 0 10%,#4a8a3b 10%)"></div>
      <h3 class="product-name">Product Name</h3>
      <p class="product-sub">Cupidatat non proident</p>
      <div class="stars">★★★★★</div>
      <div class="product-foot"><span class="price">$8.00</span><a class="btn-outline">Add to Cart</a></div>
    </article>
  </div>
</section>

<section class="welcome">
  <h2>Welcome to Lumiva Books</h2>
  <p>Lorem ipsum dolor sit amet, consectetur adipisicing elit, sed do eiusmod tempor incididunt ut labore et doloreasdes magna aliqua. Ut enim ad minim veniam, quis nostrud exercitation ullamco laboris nisi ut aliquip ex ea commodalo consequat. Duis aute irure dolor in reprehenderit in voluptate velit esse cillum dolore eu fugiat nulla pariatur. Excepteur sint occaecat cupidatat non proident, sunt in culpa qui officia deserunt mollit anim id est laborum. ..</p>
  <a class="btn-light">Read More</a>
</section>

<section class="testimonials">
  <h2 class="section-title">Testimonials</h2>
  <svg class="slider-arrow" style="left:165px" width="16" height="24" viewBox="0 0 16 24"><path d="M13 2 3 12l10 10" stroke="#6ab445" stroke-width="4" fill="none"/></svg>
  <div class="testimonial-box">
    <div class="quote-mark">“</div>
    <p>Lorem ipsum dolor sit amet, consectetur adipisicing elit, sed do eiusmod tempor incididunt ut labore et doloreasdes magna aliqua. Ut enim ad minim veniam, quis nostrud exercitation ullamco laboris nisi ut aliquip ex ea commodalo consequat.</p>
    <div class="testimonial-author">-Name Heading</div>
  </div>
  <svg class="slider-arrow" style="left:1019px" width="16" height="24" viewBox="0 0 16 24"><path d="M3 2l10 10L3 22" stroke="#6ab445" stroke-width="4" fill="none"/></svg>
</section>

<section class="features">
  <div class="feature">
    <svg width="62" height="52" viewBox="0 0 62 52"><g fill="#333" stroke="#fff" stroke-width="2"><rect x="20" y="2" width="22" height="20"/><rect x="4" y="24" width="22" height="22"/><rect x="30" y="24" width="22" height="22"/></g></svg>
    <span class="feature-text">100+ Online<br>Products</span>
  </div>
  <div class="feature">
    <svg width="48" height="48" viewBox="0 0 48 48"><circle cx="24" cy="24" r="21" fill="#333"/><path d="M14 12c6 2 8 6 6 10s2 6 0 10M30 10c-2 5 4 6 8 8M28 30c4 0 6 4 4 9" stroke="#fff" stroke-width="3" fill="none"/></svg>
    <span class="feature-text">Worldwide<br>Delivery</span>
  </div>
  <div class="feature">
    <svg width="58" height="44" viewBox="0 0 58 44"><rect x="2" y="6" width="32" height="24" fill="#333"/><path d="M36 14h10l8 9v7H36z" fill="#333"/><circle cx="13" cy="34" r="6" fill="#333" stroke="#fff" stroke-width="2"/><circle cx="44" cy="34" r="6" fill="#333" stroke="#fff" stroke-width="2"/></svg>
    <span class="feature-text">Free &amp; Easy<br>Shipping</span>
  </div>
  <div class="feature">
    <svg width="56" height="46" viewBox="0 0 56 46"><path d="M20 4 2 20l18 16v-9c14 0 24 4 32 16-2-16-12-28-32-30z" fill="#333"/></svg>
    <span class="feature-text">Easy Return<br>Policy</span>
  </div>
</section>

<footer class="site-footer">
  <div class="footer-brand">Lumiva Books</div>
  <div class="footer-col" style="left:301px"><h3>Quick Links</h3><ul><li>Home</li><li>About Us</li><li>Books</li><li>Shop</li><li>Reviews</li><li>Contact Us</li></ul></div>
  <div class="footer-col" style="left:496px"><h3>Support</h3><ul><li>Aliquam sapien</li><li>Justo commodo</li><li>Pellentesque vel</li><li>Feugiat sit</li></ul></div>
  <div class="footer-col" style="left:692px"><h3>My Account</h3><ul><li>Log In</li><li>Register</li><li>My Account</li><li>Wishlist</li><li>Help</li></ul></div>
  <div class="footer-col" style="left:884px">
    <h3>Email Subscribe</h3>
    <div class="email-field">Email Address</div>
    <a class="btn-signup">SIGN UP</a>
    <div class="social" aria-label="Social media links"><span></span><span></span><span></span><span></span></div>
  </div>
</footer>
<div class="footer-base">Copyright © 2019. Company Name. All Right Reserved</div>

</body>
</html>
```